Webshop for furniture and lamps

We need a design for a web shop with APP that should have two options:
1-Webshop in general which should attract to private customer in general and
2-Website that is meant to attract big customers as hotels and restaurants who would have their own customerize login.

That's the idea behind the shop.

It should be diveded into 4 parts
vintage furniture
rattan set outdoor and indoor
lamps and
wooden wall decor

The name of the shop is loma vereda!

Please kindly make me an offer.

Reason: Dear designers, so far there hasn't been a design that really matched. Look up German web sites like www.glimmerhof-wohnen.de or www.sitzraum77.de... Haven't been convinced by designs! Sorry folks. Please submit some new ones. Kind regards Ned

```html
<!DOCTYPE html>
<html lang="en">
<head>
<meta charset="utf-8">
<title>Loma Vereda – Furniture &amp; Lamps</title>
<link href="https://fonts.googleapis.com/css2?family=Oswald:wght@400;500;600;700&family=Open+Sans:wght@400;600;700&display=swap" rel="stylesheet">
<style>
:root{
  --blue:#2a9fd8;
  --blue-light:#4db4e6;
  --dark:#3a302d;
  --darker:#2f2725;
  --wood:#4a3a33;
  --text:#4a4a4a;
  --muted:#7a7a7a;
  --white:#ffffff;
  --price:#c0392b;
  --panel:#f1f1ef;
}
*{box-sizing:border-box;margin:0;padding:0}
html,body{width:1200px;height:3252px;overflow:hidden}
body{font-family:"Open Sans",Arial,sans-serif;color:var(--text);background:var(--white);position:relative}
.head-font{font-family:"Oswald","Arial Narrow",sans-serif}
.abs{position:absolute}

/* top bar */
.topbar{position:absolute;left:0;top:0;width:1200px;height:54px;background:var(--dark);color:#cfc8c4;font-size:13px}
.topbar .welcome{position:absolute;left:95px;top:18px}
.topbar .account{position:absolute;right:95px;top:18px;display:flex;gap:34px}

/* header */
.site-header{position:absolute;left:0;top:54px;width:1200px;height:114px;background:var(--white)}
.logo{position:absolute;left:95px;top:36px;display:flex;align-items:center;gap:14px}
.logo-mark{width:48px;height:40px;background:var(--dark)}
.logo-name{font-family:"Oswald",sans-serif;font-weight:700;font-size:30px;color:var(--blue);letter-spacing:.5px}
.main-nav{position:absolute;right:95px;top:48px;display:flex;gap:26px;align-items:center;font-family:"Oswald",sans-serif;font-weight:500;font-size:14px;color:var(--dark)}

/* hero */
.hero{position:absolute;left:0;top:168px;width:1200px;height:440px;background:linear-gradient(100deg,#5b4a40 0%,#8a7565 35%,#a99583 60%,#7c6a5c 100%)}
.hero-title{position:absolute;left:125px;top:130px;color:var(--white);font-family:"Oswald",sans-serif;font-weight:700;line-height:1.08}
.hero-title .big{font-size:68px;display:block;letter-spacing:1px}
.hero-title .sub{font-size:44px;display:block;margin-top:10px}
.signin{position:absolute;left:692px;top:90px;width:408px;height:350px;background:var(--blue)}
.signin .field{position:absolute;left:38px;width:332px;height:56px;background:var(--white);color:#9a9a9a;font-size:14px;text-align:center;line-height:56px}
.signin .btn{position:absolute;left:38px;top:212px;width:332px;height:54px;background:var(--dark);color:var(--white);font-family:"Oswald",sans-serif;font-weight:600;font-size:22px;text-align:center;line-height:54px}
.slider-dot{position:absolute;left:880px;top:412px;width:34px;height:34px;border-radius:50%;background:var(--white)}
.slider-dot::after{content:"";position:absolute;left:9px;top:9px;width:16px;height:16px;border-radius:50%;background:var(--dark)}

/* section titles */
.boxed-title{position:absolute;left:50%;transform:translateX(-50%);border:3px solid currentColor;padding:0 32px;height:54px;line-height:48px;font-family:"Oswald",sans-serif;font-weight:600;font-size:20px;letter-spacing:1px;white-space:nowrap}
.read-more{font-family:"Oswald",sans-serif;font-weight:600;font-size:12px;letter-spacing:.5px}

/* category */
.category{position:absolute;left:0;top:608px;width:1200px;height:926px}
.category .boxed-title{top:71px;color:var(--dark)}
.cat-links{position:absolute;left:0;width:1200px;top:172px;text-align:center;font-size:13px;color:var(--muted)}
.cat-links .active{color:var(--blue);font-weight:700}
.cat-intro{position:absolute;left:0;width:1200px;top:196px;text-align:center;font-size:13px;color:var(--muted)}
.category .read-more{position:absolute;left:0;width:1200px;top:236px;text-align:center;color:var(--dark)}
.product{position:absolute;top:315px;width:300px;text-align:center}
.product .photo{width:280px;height:190px;margin:0 auto}
.product h3{margin-top:100px;font-family:"Oswald",sans-serif;font-weight:600;font-size:15px;color:var(--dark)}
.product .rule{width:50px;height:3px;background:#bbb;margin:10px auto 0}
.product .price{margin-top:14px;font-family:"Oswald",sans-serif;font-weight:600;font-size:17px;color:var(--price)}
.product p{margin-top:12px;font-size:12.5px;line-height:1.65;color:var(--muted)}
.shop-now{position:absolute;left:480px;top:777px;width:240px;height:50px;background:var(--blue);clip-path:polygon(0 0,100% 0,90% 100%,10% 100%);color:var(--white);font-family:"Oswald",sans-serif;font-weight:600;font-size:24px;text-align:center;line-height:50px}

/* blog */
.blog{position:absolute;left:0;top:1534px;width:1200px;height:774px;background:linear-gradient(90deg,var(--wood),#3e302a 50%,var(--wood))}
.blog .boxed-title{top:95px;color:var(--white)}
.post{position:absolute;width:300px;color:#d8d0cb}
.post .num{position:absolute;left:0;top:0;width:44px;height:44px;background:var(--blue);color:var(--white);font-family:"Oswald",sans-serif;font-weight:700;font-size:28px;text-align:center;line-height:44px}
.post h4{position:absolute;left:64px;top:8px;color:var(--white);font-family:"Oswald",sans-serif;font-weight:600;font-size:17px;white-space:nowrap}
.post .rule{position:absolute;left:64px;top:40px;width:44px;height:3px;background:#8d817b}
.post p{position:absolute;left:0;top:62px;width:300px;font-size:12px;line-height:1.7}
.post .read-more{position:absolute;left:0;top:126px;color:var(--white)}
.promo{position:absolute;left:95px;top:643px;width:1005px;height:123px;background:var(--blue)}
.promo .photo{position:absolute;left:0;top:0;width:557px;height:123px;background:linear-gradient(90deg,#6b5a44,#c8b48c 45%,#8f7a5c)}
.promo h5{position:absolute;left:575px;top:26px;color:var(--white);font-family:"Oswald",sans-serif;font-weight:700;font-size:30px}
.promo .tag{position:absolute;left:575px;top:70px;color:var(--white);font-family:"Oswald",sans-serif;font-weight:500;font-size:15px}
.promo .btn{position:absolute;left:860px;top:44px;width:106px;height:42px;border:2px solid var(--white);color:var(--white);font-family:"Oswald",sans-serif;font-weight:600;font-size:13px;text-align:center;line-height:38px}

/* testimonials & video */
.social-proof{position:absolute;left:0;top:2308px;width:1200px;height:489px}
.social-proof .boxed-title{top:89px;color:var(--dark);transform:none}
.quote-box{position:absolute;left:95px;top:203px;width:503px;height:218px;background:var(--panel)}
.quote-box h6{position:absolute;left:22px;top:34px;font-family:"Oswald",sans-serif;font-weight:600;font-size:16px;color:var(--dark)}
.quote-box .rule{position:absolute;left:22px;top:68px;width:40px;height:3px;background:#bbb}
.quote-box p{position:absolute;left:22px;top:86px;width:460px;font-size:12.5px;line-height:1.7;color:var(--muted)}
.quote-nav{position:absolute;left:410px;top:174px;display:flex;gap:6px}
.quote-nav span{width:40px;height:40px;background:var(--blue);display:block}
.video{position:absolute;left:679px;top:203px;width:345px;height:218px;background:linear-gradient(180deg,#a9b9c4 0%,#6e7a63 45%,#4f4037 100%)}
.play{position:absolute;left:150px;top:86px;width:46px;height:46px;border-radius:50%;background:var(--white)}

/* features */
.features{position:absolute;left:0;top:2797px;width:1200px;height:366px;background:var(--dark)}
.feature{position:absolute;top:5px;width:335px;height:361px;background:#3f3532;text-align:center;color:#d3cbc7}
.feature .band{height:98px;background:var(--blue);display:flex;align-items:center;justify-content:center;gap:18px;color:var(--white);font-family:"Oswald",sans-serif;font-weight:600;font-size:18px}
.feature.mid .band{background:var(--blue-light)}
.feature .rule{width:44px;height:3px;background:#8d817b;margin:28px auto 0}
.feature p{font-size:12px;line-height:1.7;margin:16px auto 0;width:270px}
.cards{display:flex;gap:10px;justify-content:center;margin-top:16px}
.cards span{width:48px;height:28px;background:#e9e6e4;border-radius:3px}
.feature .btn{position:absolute;left:100px;top:252px;width:134px;height:40px;border:2px solid #bdb5b0;color:var(--white);line-height:36px}
.feature.pay .btn{top:252px}

/* footer */
.site-footer{position:absolute;left:0;top:3163px;width:1200px;height:89px;background:var(--darker);color:#bfb6b1;font-size:12px}
.site-footer .copy{position:absolute;left:95px;top:38px}
.site-footer .links{position:absolute;left:415px;top:38px;display:flex;gap:22px}
.site-footer .social{position:absolute;right:95px;top:32px;display:flex;gap:8px}
.site-footer .social span{width:24px;height:24px;background:var(--blue);display:block}
.site-footer .social span.r{background:#c0392b}
</style>
</head>
<body>

<div class="topbar">
  <div class="welcome">Marla Quint, welcome to our online store!</div>
  <div class="account"><span>Login</span><span>My Account ⌄</span><span>0 item</span><span>Checkout</span></div>
</div>

<header class="site-header">
  <div class="logo"><span class="logo-mark"></span><span class="logo-name">LOMA VEREDA</span></div>
  <nav class="main-nav">
    <span>HOME</span><span>SHOP BY BRAND</span><span>TOP SELLERS</span><span>CLEARANCE</span><span>HELP CENTER</span><span>MY FAVORITES</span>
    <svg width="16" height="16" viewBox="0 0 16 16"><circle cx="6.5" cy="6.5" r="5" fill="none" stroke="#3a302d" stroke-width="2"/><line x1="10" y1="10" x2="15" y2="15" stroke="#3a302d" stroke-width="2"/></svg>
  </nav>
</header>

<section class="hero" role="img" aria-label="Bright bedroom interior with a brick wall and a table lamp">
  <h1 class="hero-title"><span class="big">BUSSINES<br>MEMBERSHIP</span><span class="sub">PLEASE SIGN IN HERE</span></h1>
  <form class="signin">
    <div class="field" style="top:52px">type your name here</div>
    <div class="field" style="top:126px">type your email here</div>
    <div class="btn">SIGN IN</div>
  </form>
  <div class="slider-dot"></div>
</section>

<section class="category">
  <h2 class="boxed-title">SHOP BY CATEGORY</h2>
  <div class="cat-links">VINTAGE FURNITURE &nbsp;|&nbsp; <span class="active">RATTAN SET OUTDOOR AND INDOOR</span> &nbsp;|&nbsp; LAMPS &nbsp;|&nbsp; WOODEN WALL DECOR</div>
  <p class="cat-intro">sunt perspiciatis ipsam sed doloremque ipsam dolores totam unde aut illo aut veritatis explicabo dicta qua dicta verbatio dicta sunt quasi eaque rem</p>
  <div class="read-more">READ MORE</div>

  <article class="product" style="left:108px">
    <div class="photo" role="img" aria-label="Painted vintage chest of drawers" style="background:linear-gradient(135deg,#b4503a,#6c8a6a 50%,#c27a3c)"></div>
    <h3>VOLUPTATEM FUGIT AUT</h3><div class="rule"></div><div class="price">$876.00</div>
    <p>ipsum dolor sit amet <b>voluptatem</b> fugit aut<br>ut nemo nim ipsam quasi voluptatem</p>
  </article>
  <article class="product" style="left:450px">
    <div class="photo" role="img" aria-label="Weathered wooden storage trunk" style="background:linear-gradient(135deg,#8a7358,#b7a88a 50%,#6e8c88)"></div>
    <h3>VOLUPTATEM FUGIT AUT</h3><div class="rule"></div><div class="price">$876.00</div>
    <p>ipsum dolor sit amet voluptatem fugit aut<br>ut nemo <b>nim ipsam</b> quasi voluptatem</p>
  </article>
  <article class="product" style="left:762px">
    <div class="photo" role="img" aria-label="Rustic wooden cabinet with painted drawers" style="background:linear-gradient(135deg,#5a4030,#7a5a42 50%,#9c6a3e)"></div>
    <h3>VOLUPTATEM FUGIT AUT</h3><div class="rule"></div><div class="price">$876.00</div>
    <p>ipsum <b>dolor sit</b> amet voluptatem fugit aut<br>ut nemo nim ipsam quasi voluptatem</p>
  </article>

  <div class="shop-now">SHOP NOW</div>
</section>

<section class="blog">
  <h2 class="boxed-title">LATES NEWS FROM BLOG</h2>
  <article class="post" style="left:95px;top:209px"><span class="num">1</span><h4>AMET VOLUPTATEM</h4><span class="rule"></span><p>Lorem ipsum dolor sit amet rem illo omnis aperiam sit ipsam ipsa odit aut aspernatur veritatis unde enim accusantium laudantium sit</p><span class="read-more">READ MORE</span></article>
  <article class="post" style="left:451px;top:209px"><span class="num">2</span><h4>AMET VOLUPTATEM</h4><span class="rule"></span><p>Lorem ipsum dolor sit amet rem illo omnis aperiam sit ipsam ipsa odit aut aspernatur veritatis unde enim accusantium laudantium sit</p><span class="read-more">READ MORE</span></article>
  <article class="post" style="left:806px;top:209px"><span class="num">3</span><h4>AMET VOLUPTATEM</h4><span class="rule"></span><p>Lorem ipsum dolor sit amet rem illo omnis aperiam sit ipsam ipsa odit aut aspernatur veritatis unde enim accusantium laudantium sit</p><span class="read-more">READ MORE</span></article>
  <article class="post" style="left:95px;top:421px"><span class="num">4</span><h4>AMET VOLUPTATEM</h4><span class="rule"></span><p>Lorem ipsum dolor sit amet rem illo omnis aperiam sit ipsam ipsa odit aut aspernatur veritatis unde enim accusantium laudantium sit</p><span class="read-more">READ MORE</span></article>
  <article class="post" style="left:451px;top:421px"><span class="num">5</span><h4>AMET VOLUPTATEM</h4><span class="rule"></span><p>Lorem ipsum dolor sit amet rem illo omnis aperiam sit ipsam ipsa odit aut aspernatur veritatis unde enim accusantium laudantium sit</p><span class="read-more">READ MORE</span></article>
  <article class="post" style="left:806px;top:421px"><span class="num">6</span><h4>AMET VOLUPTATEM</h4><span class="rule"></span><p>Lorem ipsum dolor sit amet rem illo omnis aperiam sit ipsam ipsa odit aut aspernatur veritatis unde enim accusantium laudantium sit</p><span class="read-more">READ MORE</span></article>

  <aside class="promo">
    <div class="photo" role="img" aria-label="Rattan outdoor lounge chairs with striped cushions"></div>
    <h5>OUTSIDE FURNITURE</h5>
    <div class="tag">BIG SAVINGS ON QUALITY ITEMS</div>
    <div class="btn">SHOP NOW</div>
  </aside>
</section>

<section class="social-proof">
  <h2 class="boxed-title" style="left:218px">WHAT THEY SAYS</h2>
  <h2 class="boxed-title" style="left:720px">WATCH OUR VIDEO</h2>
  <blockquote class="quote-box">
    <h6>TOBI RENN, 25 YO</h6><span class="rule"></span>
    <p>Lorem ipsum dolor sit amet rem eos illo omnis aperiam sit ipsa odit aut aspernatur veritatis unde unde, sed enim accusan tium laudantium totam rem perspiciatis ipsam sed doloremque</p>
    <div class="quote-nav">
      <span><svg width="40" height="40" viewBox="0 0 40 40"><polyline points="23,12 15,20 23,28" fill="none" stroke="#fff" stroke-width="3"/></svg></span>
      <span><svg width="40" height="40" viewBox="0 0 40 40"><polyline points="17,12 25,20 17,28" fill="none" stroke="#fff" stroke-width="3"/></svg></span>
    </div>
  </blockquote>
  <div class="video" role="img" aria-label="Video still of a rattan dining set on a wooden deck">
    <span class="play"><svg width="46" height="46" viewBox="0 0 46 46"><polygon points="18,14 32,23 18,32" fill="#3a302d"/></svg></span>
  </div>
</section>

<section class="features">
  <div class="feature pay" style="left:95px">
    <div class="band"><svg width="30" height="30" viewBox="0 0 30 30"><rect x="3" y="6" width="24" height="18" fill="none" stroke="#fff" stroke-width="2.5"/><line x1="3" y1="12" x2="27" y2="12" stroke="#fff" stroke-width="3"/></svg>PAYMENT METHOD</div>
    <div class="rule"></div>
    <p>Lorem ipsum dolor sit amet, omnis aperiam</p>
    <div class="cards"><span></span><span></span><span></span><span></span></div>
    <div class="btn read-more">READ MORE</div>
  </div>
  <div class="feature mid" style="left:430px">
    <div class="band"><svg width="36" height="28" viewBox="0 0 36 28"><rect x="1" y="4" width="22" height="16" fill="#fff"/><polygon points="24,9 31,9 35,15 35,20 24,20" fill="#fff"/><circle cx="8" cy="23" r="4" fill="#fff"/><circle cx="29" cy="23" r="4" fill="#fff"/></svg>FREE SHIPPING</div>
    <div class="rule"></div>
    <p>Lorem ipsum dolor sit amet, omnis aperiam sit ipsa ipsa odit aut aspernatur veritatis unde enim accusantium laudantium</p>
    <div class="btn read-more">READ MORE</div>
  </div>
  <div class="feature" style="left:765px">
    <div class="band"><svg width="26" height="30" viewBox="0 0 26 30"><path d="M6 13V9a7 7 0 0 1 14 0v4" fill="none" stroke="#fff" stroke-width="3"/><rect x="2" y="13" width="22" height="16" fill="#fff"/></svg>SECURE SHOPPING</div>
    <div class="rule"></div>
    <p>Lorem ipsum dolor sit amet, omnis aperiam sit ipsa ipsa odit aut aspernatur veritatis unde enim accusantium laudantium</p>
    <div class="btn read-more">READ MORE</div>
  </div>
</section>

<footer class="site-footer">
  <div class="copy">© 2014 <b>YOUR COMPANY</b>. ALL RIGHTS RESERVED.</div>
  <nav class="links"><span>ABOUT US</span><span>TERM AND USE</span><span>PRIVACY POLICY</span><span>FAQS</span><span>CONTACT US</span></nav>
  <div class="social"><span></span><span></span><span class="r"></span><span></span><span class="r"></span></div>
</footer>

</body>
</html>
```